Fresh, modern, fun business card for pediatric dental practice

Need a business card for fresh, modern, fun pediatric dental practice

Clean look that matches our website's font and colors

We prefer the look of curved corners on business cards

Target Market(s)

parents (mothers) of young children, professionals, mid-high class

Industry/Entity Type

Dental

Contact Information for Business Card

Maplebrook Pediatric Dentistry
482 Quarry Lane
Suite 517
Alder Springs, PA 17590
717.555.0193
www.maplebrookkidsdental.example

Mei-Ran Tsai, DMD
Corinne Walbeck, DMD
(we are working on our email address, but we would like that on the card as well)

Font styles to use
Sans Serif

Requirements
Must have
• All info; we would also like to make cards for individual staff members
• colors from our website and color palatte, attatched
• use same font and design as website for branding
Nice to have
• clean, simple card that has a pop of color
• we would like to see a few designs with our tag line "where smiles get brighter"
• we are not sure if we want to have it on there or not
• we would like to see a few designs incorporating the ribbon graphic on our website where the word WELCOME is

```html
<!DOCTYPE html>
<html lang="en">
<head>
<meta charset="utf-8">
<title>Maplebrook Pediatric Dentistry – Business Card</title>
<link href="https://fonts.googleapis.com/css2?family=Lato:wght@400;700&family=Oswald:wght@600&display=swap" rel="stylesheet">
<style>
  :root {
    --backdrop: #1b1b1b;
    --card-top: #2e2e2e;
    --card-bottom: #232323;
    --sun-yellow: #f6b91e;
    --berry: #c42b83;
    --ink-light: #f2f2f2;
    --ink-muted: #9a9a9a;
  }
  * { margin: 0; padding: 0; box-sizing: border-box; }
  html, body {
    width: 1200px; height: 900px; overflow: hidden;
    background: var(--backdrop);
    font-family: "Lato", Arial, sans-serif;
  }
  .stage {
    position: relative; width: 1200px; height: 900px;
    display: flex; flex-direction: column; align-items: center; justify-content: center;
    gap: 40px;
  }
  .card {
    position: relative; width: 640px; height: 366px;
    border-radius: 18px; overflow: hidden;
    background: linear-gradient(160deg, var(--card-top), var(--card-bottom));
    box-shadow: 0 10px 30px rgba(0,0,0,.45);
  }
  .card__stripe {
    position: absolute; left: 0; right: 0; bottom: 0; height: 7px;
    background: var(--sun-yellow);
  }
  /* Front */
  .card--front .brand {
    position: absolute; left: 0; right: 0; top: 128px;
    display: flex; align-items: center; justify-content: center; gap: 14px;
  }
  .brand__dot {
    width: 18px; height: 18px; border-radius: 50%;
    background: var(--ink-muted);
  }
  .brand__name {
    font-size: 30px; font-weight: 400; letter-spacing: 1px;
    color: var(--ink-muted);
  }
  .card--front .site {
    position: absolute; left: 0; right: 0; bottom: 52px; text-align: center;
    font-size: 17px; letter-spacing: 2px; color: var(--ink-light);
  }
  .site__domain { color: var(--sun-yellow); }
  /* Back */
  .person {
    position: absolute; left: 36px; top: 112px; width: 265px; text-align: right;
  }
  .person__name {
    font-family: "Oswald", "Arial Narrow", sans-serif; font-weight: 600;
    font-size: 34px; letter-spacing: .5px; color: var(--sun-yellow); line-height: 1.1;
  }
  .person__title {
    font-size: 18px; color: var(--ink-light); margin-top: 6px; letter-spacing: 1px;
  }
  .divider {
    position: absolute; left: 318px; top: 120px; width: 2px; height: 64px;
    background: var(--berry);
  }
  .contact {
    position: absolute; left: 338px; top: 118px; list-style: none;
    font-size: 15px; color: var(--ink-light); line-height: 24px;
  }
  .contact li { display: flex; align-items: center; gap: 10px; white-space: nowrap; }
  .contact svg { width: 14px; height: 14px; fill: var(--sun-yellow); flex: none; }
  .practice {
    position: absolute; left: 44px; bottom: 42px;
  }
  .practice__name {
    font-size: 18px; font-weight: 700; letter-spacing: 1px;
    color: var(--sun-yellow); text-transform: uppercase; margin-left: 70px;
  }
  .practice__address {
    font-size: 19px; color: var(--ink-light); margin-top: 2px; white-space: nowrap;
  }
</style>
</head>
<body>
<main class="stage">
  <section class="card card--front" aria-label="Card front">
    <div class="brand">
      <span class="brand__dot"></span>
      <span class="brand__name">Maplebrook Pediatric Dentistry</span>
    </div>
    <p class="site">www.<span class="site__domain">maplebrookkidsdental</span>.example</p>
    <div class="card__stripe"></div>
  </section>

  <section class="card card--back" aria-label="Card back">
    <div class="person">
      <h1 class="person__name">CORINNE WALBECK</h1>
      <p class="person__title">DMD</p>
    </div>
    <div class="divider"></div>
    <ul class="contact">
      <li>
        <svg viewBox="0 0 24 24" aria-hidden="true"><path d="M6.6 10.8a15.1 15.1 0 0 0 6.6 6.6l2.2-2.2c.3-.3.7-.4 1-.2 1.1.4 2.3.6 3.6.6.6 0 1 .4 1 1V20c0 .6-.4 1-1 1A17 17 0 0 1 3 4c0-.6.4-1 1-1h3.5c.6 0 1 .4 1 1 0 1.3.2 2.5.6 3.6.1.3 0 .7-.2 1z"/></svg>
        717.555.0193
      </li>
      <li>
        <svg viewBox="0 0 24 24" aria-hidden="true"><path d="M2 5h20v14H2z M2 5l10 8 10-8" /></svg>
        info@maplebrookkidsdental.example
      </li>
      <li>
        <svg viewBox="0 0 24 24" aria-hidden="true"><path d="M12 2a10 10 0 1 0 0 20 10 10 0 0 0 0-20zm6.9 6h-3a15.7 15.7 0 0 0-1.4-3.6A8 8 0 0 1 18.9 8zM12 4c.8 1.2 1.5 2.5 1.9 4h-3.8c.4-1.5 1.1-2.8 1.9-4zM4.3 14a8.2 8.2 0 0 1 0-4h3.4a16.5 16.5 0 0 0 0 4zm.8 2h3a15.7 15.7 0 0 0 1.4 3.6A8 8 0 0 1 5.1 16zm3-8h-3a8 8 0 0 1 4.4-3.6C8.9 5.5 8.4 6.7 8.1 8zM12 20c-.8-1.2-1.5-2.5-1.9-4h3.8c-.4 1.5-1.1 2.8-1.9 4zm2.3-6H9.7a14.7 14.7 0 0 1 0-4h4.6a14.7 14.7 0 0 1 0 4zm.3 5.6c.6-1.1 1.1-2.3 1.4-3.6h3a8 8 0 0 1-4.4 3.6zm1.7-5.6a16.5 16.5 0 0 0 0-4h3.4a8.2 8.2 0 0 1 0 4z"/></svg>
        www.maplebrookkidsdental.example
      </li>
    </ul>
    <div class="practice">
      <p class="practice__name">Maplebrook Pediatric Dentistry</p>
      <p class="practice__address">482 Quarry Lane Suite 517 Alder Springs, PA 17590</p>
    </div>
    <div class="card__stripe"></div>
  </section>
</main>
</body>
</html>
```